Business Card (double-sided) and Stationary Design for dental office

1) Business Card Design: We need a business card design for a dental specialty office.
Texts should contain:
The name of our office "Brindle Oaks Orthodontics"
Tagline: "Specialist in Orthodontic and Maxillofacial Orthopedics"
Tag line: "Creating "Tolvering" smiles for Children and Adults"
Doctor name: "Doctor Name"
Office Address:
"123 Street Name
City, State Zip code"
Office email address: office@brindleoaksortho.com
Website: www.brindleoaksortho.com

We will provide the full office address once the design is selected
Theme: beach, paradise, coastal, wave
We would like to have some creativity in design. Some acceptable ideas: front page: logo and office name. Back page: more detail information, and map to office in form of an island. Please see sample from our other location, but you DON'T HAVE TO USE OR COPY THE SAME CONCEPT.

IF POSSIBLE, PLEASE SUBMIT AT LEAST TWO CONCEPTS: ONE WITH THE BACK LOOKING SIMILAR TO WHAT IS IN THE SAMPLE, AND ONE DIFFERENT.

Color: designer to choose. We have different shade of blues and sand color in our office. Please see logo.

2) Please also design a matching set of stationary that compliment the business card and our logo.

Target Market(s)

Dental

Contact Information for Business Card

See descriptions

Font styles to use
Other font styles liked:
• Matching texts in logo

Colors
0054AA
0677BA
7BADD7
CADEEF
E8F1F8
0094D4
00A9DD
6FCCEA
C7EBF8
E9F6FB
00AB8E
00BBA5
67D7C9
C6EFE9
E9F9F6

Requirements
Must have
• Double-sided
Nice to have
• Beach coastal theme
Should not have
• Any shape or drawing of of tooth or teeth. We don’t need these. You don't necessarily have to just cut and paste the logo art and text as a whole, you have the liberty to rearrange the text.

```html
<!DOCTYPE html>
<html lang="en">
<head>
<meta charset="utf-8">
<title>Brindle Oaks Stationery</title>
<link rel="stylesheet" href="https://fonts.googleapis.com/css2?family=Montserrat:ital,wght@0,400;0,600;0,700;1,700&family=Itim&display=swap">
<style>
  :root{
    --backdrop:#999596;
    --paper:#f1f0f1;
    --teal-deep:#3a8ea6;
    --mint:#7fcfbd;
    --brand:#2f8fa6;
    --ink:#3a3a3a;
    --faint:rgba(58,142,166,.12);
    --navy:#1c2a55;
    --scene-top:#9fd3ea;
    --scene-bottom:#e4b46a;
  }
  *{margin:0;padding:0;box-sizing:border-box}
  html,body{width:1200px;height:826px;overflow:hidden;background:var(--backdrop);font-family:"Montserrat",sans-serif;color:var(--ink)}
  .sheet{position:absolute;background:var(--paper);overflow:hidden;box-shadow:0 2px 6px rgba(0,0,0,.25)}
  .band{position:absolute;left:0;right:0;background:linear-gradient(90deg,var(--teal-deep) 0%,var(--teal-deep) 45%,var(--mint) 62%,var(--mint) 100%)}
  .mark-dot{position:absolute;border-radius:50%;background:var(--brand);border:3px solid #fff}
  .wordmark{position:absolute;font-family:"Montserrat",sans-serif;font-weight:600;color:var(--brand);white-space:nowrap;text-align:center;transform:translateX(-50%);line-height:1}
  .subline{position:absolute;font-weight:600;color:var(--mint);white-space:nowrap;transform:translateX(-50%);letter-spacing:.06em;font-size:6px}
  .ghost{position:absolute;border-radius:50%;background:var(--faint)}

  /* letterhead */
  .letterhead{left:59px;top:111px;width:462px;height:645px}
  .letterhead .band{top:36px;height:45px}
  .salutation{position:absolute;left:42px;top:181px;font-size:11.5px}
  .letter-body{position:absolute;left:42px;top:213px;width:382px;font-size:6.4px;line-height:9.8px;color:#666;text-align:justify}
  .letter-body p{margin-bottom:9.5px}
  .closing{position:absolute;left:42px;top:424px;font-size:6.4px;color:#666}
  .letter-foot{position:absolute;left:0;right:0;top:605px;text-align:center;font-size:8.6px;line-height:12px}

  /* business card */
  .biz-card{left:550px;top:120px;width:288px;height:164px}
  .biz-card .band{top:28px;height:27px}
  .holder{position:absolute;left:25px;top:35px;font-family:"Itim",cursive;color:#fff;font-size:12px;letter-spacing:.03em}
  .contact{position:absolute;left:27px;top:116px;font-size:6.5px;line-height:8.3px;list-style:none}
  .contact li{display:flex;align-items:center;gap:3px}
  .contact svg{width:5px;height:5px;fill:var(--teal-deep)}
  .card-address{position:absolute;right:28px;top:116px;text-align:right;font-size:6.5px;line-height:8.3px}

  /* appointment card */
  .appt-card{left:862px;top:120px;width:288px;height:164px}
  .beach-scene{position:absolute;inset:0;background:linear-gradient(180deg,var(--scene-top) 0%,var(--scene-bottom) 100%)}
  .appt-card .mark-dot{background:#3a2418;border-color:#fff}
  .appt-card .wordmark{color:#3a2418}
  .appt-box{position:absolute;left:14px;top:76px;width:178px;height:50px;background:rgba(255,255,255,.85);border-radius:4px;padding:5px 6px;font-size:5.6px;color:#222}
  .appt-box h3{font-size:6px;font-weight:700;margin-bottom:5px}
  .fill-line{display:flex;gap:2px;margin-bottom:6px}
  .fill-line span.rule{flex:1;border-bottom:.6px dotted #555}
  .appt-tag{position:absolute;left:0;right:0;text-align:center;font-weight:700;color:var(--navy);white-space:nowrap}
  .appt-tag.spec{top:139px;font-size:6px;left:-40px}
  .appt-tag.promise{top:147px;font-size:7px;font-style:italic;left:-40px}

  /* envelopes */
  .env-back{left:602px;top:337px;width:529px;height:240px}
  .env-flap{position:absolute;left:0;top:0;width:529px;height:76px}
  .env-back .mark-dot{background:var(--teal-deep)}
  .env-front{left:564px;top:510px;width:530px;height:242px}
  .env-front .band{top:27px;height:46px;background:linear-gradient(90deg,var(--teal-deep) 0%,var(--teal-deep) 10%,var(--mint) 22%,var(--mint) 100%)}
  .return-address{position:absolute;left:26px;top:106px;font-size:9px;line-height:11.5px;letter-spacing:.02em}
</style>
</head>
<body>

<!-- Letterhead -->
<section class="sheet letterhead">
  <div class="ghost" style="left:125px;top:205px;width:210px;height:210px"></div>
  <div class="band"></div>
  <div class="mark-dot" style="left:206px;top:33px;width:50px;height:50px"></div>
  <div class="wordmark" style="left:231px;top:110px;font-size:15px">BrindleOaks</div>
  <div class="subline" style="left:231px;top:127px">Pediatric Dentistry &amp; Orthodontics</div>
  <p class="salutation">Dear Mr. Ferrow,</p>
  <div class="letter-body">
    <p>Lorem ipsum dolor sit amet, consectetur adipiscing elit. Donec orci purus, luctus vitae dignissim eu, iaculis sed purus. Vivamus faucibus, ipsum nec aliquet viverra, leo mauris condimentum ligula, sit amet sagittis enim ligula quis arcu. Nam egestas tortor id nisi porttitor mattis. In tortor ante, ultricies in suscipit a, tempus non massa. Vivamus et auctor mi. Fusce vel massa nulla. Phasellus nec eros mauris, et scelerisque orci.</p>
    <p>Donec malesuada orci vitae nulla accumsan porta a id massa. Quisque accumsan iaculis magna sit amet fringilla. Maecenas consequat, magna eget tincidunt semper, odio nibh rutrum mi, id feugiat ante nisi eu risus. Vestibulum nunc orci, rhoncus a placerat in, ultricies in mi. Cras mattis varius eros, vel fringilla nisi suscipit eget. Quisque scelerisque sagittis nulla at porttitor.</p>
    <p>Sed id augue vitae urna euismod commodo aliquet a quam. Pellentesque arcu velit, cursus et malesuada ut, consequat et diam. Nullam erat sem, rhoncus id ullamcorper vitae, rhoncus et arcu. In ultricies ultricies nulla, ut rutrum nisi iaculis at. Donec eu magna a metus ornare faucibus. Fusce aliquet faucibus ultricies. Morbi semper, est id tincidunt gravida, sem arcu adipiscing lacus, ac bibendum nulla leo eu purus. Quisque nec diam sed risus consectetur accumsan quis quis nibh. Vestibulum id purus lorem.</p>
    <p>It is a long established fact that a reader will be distracted by the readable content of a page when looking at its layout. The point of using Lorem Ipsum is that it has a more-or-less normal distribution of letters, as opposed to using 'Content here, content here', making it look like readable English. Many desktop publishing packages</p>
  </div>
  <p class="closing">Sincerely,</p>
  <p class="letter-foot">Brindle Oaks Dentistry 123 Street Name, City, State Zip code<br>P. 555-014-2837 E. office@brindleoaksortho.com W. brindleoaksortho.com</p>
</section>

<!-- Business card -->
<section class="sheet biz-card">
  <div class="ghost" style="left:-10px;top:90px;width:110px;height:110px"></div>
  <div class="band"></div>
  <p class="holder">Daniel Ferrow</p>
  <div class="mark-dot" style="left:191px;top:21px;width:40px;height:40px"></div>
  <div class="wordmark" style="left:211px;top:64px;font-size:11.5px">BrindleOaks</div>
  <div class="subline" style="left:211px;top:77px;font-size:4.5px">Pediatric Dentistry &amp; Orthodontics</div>
  <ul class="contact">
    <li><svg viewBox="0 0 10 10"><path d="M2 0h2l1 3-1.5 1a6 6 0 0 0 2.5 2.5L7 5l3 1v2c0 1-1 2-2 2C4 10 0 6 0 2 0 1 1 0 2 0z"/></svg>555-014-2837</li>
    <li><svg viewBox="0 0 10 10"><path d="M0 2h10v6H0zM0 2l5 3 5-3"/></svg>office@brindleoaksortho.com</li>
    <li><svg viewBox="0 0 10 10"><circle cx="5" cy="5" r="5"/></svg>brindleoaksortho.com</li>
  </ul>
  <p class="card-address">Brindle Oaks Dentistry<br>123 Street Name<br>City, State Zip code</p>
</section>

<!-- Appointment card -->
<section class="sheet appt-card">
  <div class="beach-scene" role="img" aria-label="Illustrated tropical beach with palm trees, sea and an island map to the office"></div>
  <div class="mark-dot" style="left:76px;top:20px;width:32px;height:32px"></div>
  <div class="wordmark" style="left:92px;top:56px;font-size:11px">BrindleOaks</div>
  <div class="subline" style="left:92px;top:67px;font-size:4px;color:#3a2418">Pediatric Dentistry &amp; Orthodontics</div>
  <div class="appt-box">
    <h3>SEE YOU AT YOUR NEXT APPOINTMENT!</h3>
    <div class="fill-line">For<span class="rule"></span></div>
    <div class="fill-line">Date<span class="rule"></span>Time<span class="rule"></span></div>
  </div>
  <p class="appt-tag spec">Specialist in Orthodontic &amp; Maxillofacial Orthopedics</p>
  <p class="appt-tag promise">Creating "Tolvering" smiles for Children &amp; Adults</p>
</section>

<!-- Envelope back -->
<section class="sheet env-back">
  <svg class="env-flap" viewBox="0 0 529 76" preserveAspectRatio="none">
    <path d="M0 0H529V52Q529 76 505 76H24Q0 76 0 52Z" fill="var(--teal-deep)"/>
  </svg>
  <div class="mark-dot" style="left:231px;top:15px;width:44px;height:44px"></div>
</section>

<!-- Envelope front -->
<section class="sheet env-front">
  <div class="ghost" style="left:376px;top:49px;width:186px;height:186px"></div>
  <div class="band"></div>
  <div class="mark-dot" style="left:63px;top:24px;width:50px;height:50px"></div>
  <div class="wordmark" style="left:88px;top:79px;font-size:15px">BrindleOaks</div>
  <div class="subline" style="left:88px;top:95px">Pediatric Dentistry &amp; Orthodontics</div>
  <p class="return-address">Brindle Oaks Dentistry<br>123 Street Name, City, State Zip code</p>
</section>

</body>
</html>
```